Lifecoach needs website design based on a standard Wordpress theme

I need a website for my new lifecoaching business that can be easily implemented in Wordpress, it needs to be compatible with a standard Wordpress theme. So I can place the pictures, texts etc. in a standard theme of Wordpress.

I want the design to be a very good feeling and playfull one, based on my logo.

Target Market(s)

I will coach people to reach their goals and dreams in life.

Industry/Entity Type

Business

Requirements
Must have
• Can be easy implemented in Wordpress.
Nice to have
• Photo's of nature are nice.

```html
<!DOCTYPE html>
<html lang="en">
<head>
<meta charset="utf-8">
<title>Mara van Dijk Lifecoach</title>
<link rel="stylesheet" href="https://fonts.googleapis.com/css2?family=Open+Sans:wght@400;600;700&display=swap">
<style>
:root{
  --sky-top:#2fd2fd;
  --sky-bottom:#94e6ff;
  --panel:#ffffff;
  --navy:#004a78;
  --heading:#0c4a72;
  --accent:#1a9ad6;
  --nav-line:#d3d3d3;
  --text-grey:#8a8a8a;
  --text-dark:#5c5c5c;
  --frame:#d6d6d6;
  --btn-top:#a9e3f7;
  --btn-bottom:#34b4e4;
}
*{box-sizing:border-box;margin:0;padding:0}
html,body{width:978px;height:1200px;overflow:hidden}
body{
  position:relative;
  background:linear-gradient(180deg,var(--sky-top) 0%,var(--sky-bottom) 100%);
  font-family:"Open Sans",Arial,sans-serif;
}
.page{
  position:absolute;left:107px;top:49px;width:764px;height:1082px;
  background:var(--panel);border-radius:8px;overflow:hidden;
}
.abs{position:absolute}
.line{display:block;white-space:nowrap}
.brand{left:29px;top:17px;display:flex;align-items:center;gap:10px}
.brand-dot{width:72px;height:72px;border-radius:50%;border:5px solid var(--accent)}
.brand-text{color:var(--heading)}
.brand-name{font-size:25px;font-weight:400;letter-spacing:1px;line-height:28px;text-transform:uppercase}
.brand-tag{font-size:14px;letter-spacing:1.5px;text-transform:uppercase;padding-left:52px}
.nav{left:355px;top:58px;width:378px;height:27px;border-bottom:4px solid var(--nav-line)}
.nav a{position:absolute;top:0;font-size:13.5px;color:var(--accent);text-decoration:none;line-height:20px;transform:translateX(-50%);white-space:nowrap}
.nav a.current{left:31px;width:63px;text-align:center;height:27px;border-bottom:4px solid var(--accent)}
.slider{left:27px;top:105px;width:706px;height:351px;border:1px solid var(--navy)}
.slide-art{position:absolute;left:0;top:0;width:100%;height:320px;
  background:linear-gradient(180deg,#8a6fc8 0%,#5f53c0 30%,#7e7dd4 60%,#d9dcf5 100%)}
.slide-bar{position:absolute;left:0;top:320px;width:100%;height:30px;background:#6e9dc4}
.dots{position:absolute;left:338px;top:12px;display:flex;gap:4px}
.dots span{width:8px;height:8px;background:var(--navy)}
.dots span.on{background:#fff}
h2{font-weight:400;font-size:19px;color:var(--heading)}
.photo-frame{border:1px solid var(--frame);padding:6px;background:#fff}
.photo-frame .fill{width:100%;height:100%}
.intro-title{left:27px;top:480px}
.intro-photo{left:27px;top:524px;width:162px;height:140px}
.intro-photo .fill{background:linear-gradient(180deg,#3f6fcc 0%,#9aa2b8 45%,#4f7f3a 80%,#3c6b2a 100%)}
.intro-lead{left:203px;top:520px;font-size:13px;font-weight:600;color:var(--text-dark);line-height:17px;letter-spacing:-0.1px}
.intro-body{left:203px;top:562px;font-size:10px;color:var(--text-grey);line-height:18.4px}
.feat-title{left:492px;top:480px}
.feat-list{left:492px;top:517px;list-style:none;font-size:10.5px;color:var(--heading)}
.feat-list li{height:23px;display:flex;align-items:center;gap:12px;white-space:nowrap}
.feat-list svg{width:9px;height:6px}
.col-title{top:700px}
.col-photo{top:737px;width:229px;height:135px}
.col-text{width:224px;font-size:10px;color:var(--text-grey);line-height:18.4px}
.col-text .line{text-align:justify;text-align-last:justify;white-space:normal}
.more{width:59px;height:17px;background:linear-gradient(180deg,var(--btn-top),var(--btn-bottom));
  color:#fff;font-size:10.5px;text-align:center;line-height:16px;border:1px solid #6ccbee}
.personal-photo .fill{background:linear-gradient(135deg,#d9d2c4 0%,#e8c49c 50%,#cf4d6b 100%)}
.business-photo .fill{background:linear-gradient(135deg,#d3dde3 0%,#8b7c6d 50%,#efe9e2 100%)}
.project{left:547px;width:190px;height:56px}
.project .thumb{position:absolute;left:0;top:0;width:63px;height:55px}
.project .thumb .fill{background:linear-gradient(135deg,#e3ddd4,#b07f66)}
.project h3{position:absolute;left:73px;top:0;font-size:10.5px;font-weight:600;color:var(--text-dark);white-space:nowrap}
.project p{position:absolute;left:72px;top:19px;font-size:10.5px;color:var(--text-grey);line-height:15.5px}
.footer{left:0;top:1048px;width:764px;height:34px;background:var(--navy);color:#fff;
  font-size:10.5px;text-align:center;line-height:34px}
</style>
</head>
<body>
<div class="page">
  <header>
    <div class="abs brand">
      <div class="brand-dot"></div>
      <div class="brand-text">
        <div class="brand-name">Mara van Dijk</div>
        <div class="brand-tag">Lifecoach</div>
      </div>
    </div>
    <nav class="abs nav">
      <a class="current" href="#">Home</a>
      <a href="#" style="left:108px">Services</a>
      <a href="#" style="left:194px">About us</a>
      <a href="#" style="left:272px">News</a>
      <a href="#" style="left:346px">Contact</a>
    </nav>
  </header>

  <section class="abs slider">
    <div class="slide-art" role="img" aria-label="Snowy mountain landscape with a wooden cabin and pine trees at dusk"></div>
    <div class="slide-bar"><div class="dots"><span></span><span class="on"></span><span></span></div></div>
  </section>

  <h2 class="abs intro-title">Summit sets the stage for your success</h2>
  <div class="abs photo-frame intro-photo"><div class="fill" role="img" aria-label="Rocky snow-capped mountain above a green pine forest"></div></div>
  <p class="abs intro-lead"><span class="line">Lorem Ipsum. Proin gravida nibh vel</span><span class="line">velit auctor aliquet. Aenean sollicitudin,</span></p>
  <p class="abs intro-body">
    <span class="line">Lorem Ipsum. Proin gravida nibh vel velit auctor</span>
    <span class="line">aliquet. Aenean sollicitudin, lorem quis bibendum</span>
    <span class="line">auctor, nisi elit consequat ipsum, nec sagittis sem</span>
    <span class="line">nibh id elit. Duis sed odio sit amet nibh vulputate</span>
    <span class="line">cursus a sit amet mauris. Morbi accumsan velit.</span>
  </p>

  <h2 class="abs feat-title">Featured Services</h2>
  <ul class="abs feat-list">
    <li><svg viewBox="0 0 9 6"><path d="M0 3H8M5 0.5L8 3L5 5.5" stroke="#0c4a72" fill="none"/></svg>This is Photoshop's version&nbsp; of Lorem Ipsum.</li>
    <li><svg viewBox="0 0 9 6"><path d="M0 3H8M5 0.5L8 3L5 5.5" stroke="#0c4a72" fill="none"/></svg>Proin gravida nibh vel velit auctor aliquet.</li>
    <li><svg viewBox="0 0 9 6"><path d="M0 3H8M5 0.5L8 3L5 5.5" stroke="#0c4a72" fill="none"/></svg>Aenean sollicitudin, lorem quis bibendum.</li>
    <li><svg viewBox="0 0 9 6"><path d="M0 3H8M5 0.5L8 3L5 5.5" stroke="#0c4a72" fill="none"/></svg>Consequat ipsum, nec sagittis sem nibh.</li>
    <li><svg viewBox="0 0 9 6"><path d="M0 3H8M5 0.5L8 3L5 5.5" stroke="#0c4a72" fill="none"/></svg>Duis sed odio sit amet nibh vulputate curss.</li>
    <li><svg viewBox="0 0 9 6"><path d="M0 3H8M5 0.5L8 3L5 5.5" stroke="#0c4a72" fill="none"/></svg>Morbi accumsan ipsum velit. nec tellus.</li>
  </ul>

  <h2 class="abs col-title" style="left:27px">Personal</h2>
  <div class="abs photo-frame col-photo personal-photo" style="left:28px"><div class="fill" role="img" aria-label="Smiling mother and young daughter"></div></div>
  <p class="abs col-text" style="left:28px;top:876px">
    <span class="line">Aenean sollicitudin, lorem quis bibendum</span>
    <span class="line">auctor, nisi elit consequat ipsum, nec sagitThis</span>
    <span class="line">is Photoshop's version of Lorem Ipsum. Proin</span>
    <span class="line">gravida nibh vel velit auctor aliquet. sollicitudin,</span>
  </p>
  <div class="abs more" style="left:27px;top:961px">MORE</div>

  <h2 class="abs col-title" style="left:287px">Business</h2>
  <div class="abs photo-frame col-photo business-photo" style="left:288px"><div class="fill" role="img" aria-label="Businesswoman at a desk in a meeting"></div></div>
  <p class="abs col-text" style="left:290px;top:884px">
    <span class="line">Lrem quis bibendum auctor, nisi elit consequat</span>
    <span class="line">ipsum, nec sagitThis is Photoshop's version of</span>
    <span class="line">Lorem Ipsum. Proin gravida nibh vel velit auctor</span>
    <span class="line">aliquet. sollicitudin, lorem quis bibendum</span>
  </p>
  <div class="abs more" style="left:289px;top:961px">MORE</div>

  <h2 class="abs col-title" style="left:547px">Our Project</h2>
  <div class="abs project" style="top:737px">
    <div class="photo-frame thumb"><div class="fill" role="img" aria-label="Portrait of a smiling man"></div></div>
    <h3>Lorem Ipsum Proin</h3><p><span class="line">Proin gravida nibh</span><span class="line">vel velit auctor</span></p>
  </div>
  <div class="abs project" style="top:809px">
    <div class="photo-frame thumb"><div class="fill" role="img" aria-label="Hand on a computer mouse beside a keyboard" style="background:linear-gradient(135deg,#f2f2f2,#333)"></div></div>
    <h3>Ipsum Proin Lorem</h3><p><span class="line">Proin gravida nibh</span><span class="line">vel velit auctor</span></p>
  </div>
  <div class="abs project" style="top:882px">
    <div class="photo-frame thumb"><div class="fill" role="img" aria-label="Portrait of a laughing businessman"></div></div>
    <h3>Proin Lorem Ipsum</h3><p><span class="line">Proin gravida nibh</span><span class="line">vel velit auctor</span></p>
  </div>
  <div class="abs more" style="left:548px;top:961px">MORE</div>

  <footer class="abs footer">©Mara van Dijk. All Rights Reserved.</footer>
</div>
</body>
</html>
```